SkyvornQ Business Cards and Stationary Design

Need a design for our business cards and stationary. I want to carry on the theme of the logo. I want the business cards to have a design on the back. I would like the business cards and the stationary to carry the same theme, design scheme, and branding

Target Market(s)

Airlines and Maintenance Facilities

Industry/Entity Type

Aviation

Contact Information for Business Card

Name
Position Title
Address: 4827 Trellis Hollow Road, Fort Pierce, Florida, 34951
Office Number
Mobile Number
Email
Website

Font styles to use
Serif
Sans Serif

Colors

Designer to choose colors to be used in the design.

```html
<!DOCTYPE html>
<html lang="en">
<head>
<meta charset="utf-8">
<title>SkyvornQ Business Card</title>
<link href="https://fonts.googleapis.com/css2?family=Orbitron:wght@500;600;700&family=Saira:wght@500;600&display=swap" rel="stylesheet">
<style>
  :root {
    --canvas: #2b2b2d;
    --paper: #f3f3f3;
    --navy: #0b2a52;
    --band-light: #0a86cf;
    --ink: #4a4a4a;
    --icon: #0b2a52;
    --white: #ffffff;
    --back-center: #08a6e8;
    --back-edge: #0a3577;
  }
  * { margin: 0; padding: 0; box-sizing: border-box; }
  html, body { width: 1200px; height: 960px; overflow: hidden; }
  body { background: var(--canvas); position: relative; font-family: "Saira", Arial, sans-serif; }

  .card { position: absolute; width: 600px; height: 343px; border-radius: 20px; overflow: hidden; }

  .card-front { left: 314px; top: 113px; background: var(--paper); }
  .brand-band {
    position: absolute; left: 0; top: 44px; width: 100%; height: 72px;
    background: linear-gradient(90deg, var(--band-light) 0, var(--navy) 110px, var(--navy) 100%);
  }
  .wordmark {
    position: absolute; left: 60px; top: 128px; line-height: 26px; white-space: nowrap;
    font-family: "Orbitron", Arial, sans-serif; font-weight: 700; font-size: 23px; letter-spacing: 4px;
    color: var(--navy);
  }
  .holder { position: absolute; left: 379px; top: 64px; color: var(--white); font-family: "Orbitron", Arial, sans-serif; white-space: nowrap; }
  .holder-name { font-size: 13px; font-weight: 600; letter-spacing: 2.5px; line-height: 18px; }
  .holder-title { font-size: 9.5px; font-weight: 600; letter-spacing: 1.8px; line-height: 12px; margin-top: 2px; }

  .address { position: absolute; left: 379px; top: 167px; font-size: 13.5px; line-height: 18px; font-weight: 600; color: var(--ink); font-style: normal; }
  .contacts { position: absolute; left: 379px; top: 233px; list-style: none; }
  .contacts li { display: flex; align-items: center; height: 19.5px; font-size: 13.5px; font-weight: 600; color: var(--ink); white-space: nowrap; }
  .contacts li.small { font-size: 12.5px; }
  .contacts svg { width: 13px; height: 13px; margin-right: 9px; flex: none; }

  .card-back {
    left: 311px; top: 472px;
    background: radial-gradient(ellipse 360px 300px at 295px 165px, var(--back-center) 0%, #0873c2 55%, var(--back-edge) 100%);
  }
  .back-brand { position: absolute; right: 34px; top: 272px; text-align: right; color: var(--white); white-space: nowrap; }
  .back-wordmark { font-family: "Orbitron", Arial, sans-serif; font-weight: 700; font-size: 23px; letter-spacing: 4px; line-height: 28px; }
  .back-web { font-size: 13px; letter-spacing: 4px; line-height: 16px; margin-top: 1px; }
</style>
</head>
<body>
  <section class="card card-front" aria-label="Business card front">
    <div class="brand-band"></div>
    <div class="wordmark">SKYVORNQ</div>
    <div class="holder">
      <div class="holder-name">DORIAN KESSLER</div>
      <div class="holder-title">CEO/FOUNDER</div>
    </div>
    <address class="address">4827 Trellis Hollow<br>Road, Fort Pierce,<br>Florida, 34951</address>
    <ul class="contacts">
      <li>
        <svg viewBox="0 0 16 16"><path fill="var(--icon)" d="M3.6 1.2l2.3 2.6-1.4 2a9 9 0 0 0 5.7 5.7l2-1.4 2.6 2.3-1.6 2.4C7.6 14.6 1.4 8.4 1.2 2.8z"/></svg>
        555 210 4817
      </li>
      <li>
        <svg viewBox="0 0 16 16"><rect x="4" y="0.8" width="8" height="14.4" rx="1.5" fill="var(--icon)"/><rect x="5.4" y="2.6" width="5.2" height="9" fill="var(--paper)"/></svg>
        555 302 7741
      </li>
      <li class="small">
        <svg viewBox="0 0 16 16"><rect x="1" y="3.5" width="14" height="9" fill="var(--icon)"/><path d="M1.5 4l6.5 5 6.5-5" stroke="var(--paper)" stroke-width="1.2" fill="none"/></svg>
        info@skyvornq.com
      </li>
      <li class="small">
        <svg viewBox="0 0 16 16"><circle cx="8" cy="8" r="7" fill="var(--icon)"/><path d="M8 1v14M1 8h14M3 4.5c3 1.2 7 1.2 10 0M3 11.5c3-1.2 7-1.2 10 0" stroke="var(--paper)" stroke-width="1" fill="none"/></svg>
        www.skyvornq.com
      </li>
    </ul>
  </section>

  <section class="card card-back" aria-label="Business card back">
    <div class="back-brand">
      <div class="back-wordmark">SKYVORNQ</div>
      <div class="back-web">www.skyvornq.com</div>
    </div>
  </section>
</body>
</html>
```